Corvane Capital Business Cards

These are professional business cards that are for my family office.
Put fake emails and phone numbers as of now until I finalize those components. This family office controls my families investments, assets, and future. The cards should be professional.
..
.
.
.
I just uploaded another variation of a logo I would like to see as a business card to I am inbeteen which logo to use

Target Market(s)

business

Industry/Entity Type

business

Contact Information for Business Card

Professional, wealth related, finance related.

Requirements
Must have
• Logo

```html
<!DOCTYPE html>
<html lang="en">
<head>
<meta charset="utf-8">
<title>Corvane Capital Business Cards</title>
<link rel="stylesheet" href="https://fonts.googleapis.com/css2?family=Cinzel:wght@400;500&family=Montserrat:wght@300;400;600&display=swap">
<style>
  :root {
    --page-bg: #e4e0d9;
    --card-navy: #1a1f2b;
    --ink-white: #f4f4f2;
    --ink-grey: #a9abb0;
    --ink-soft: #d8d9dc;
    --back-mark: #2c3344;
  }
  * { margin: 0; padding: 0; box-sizing: border-box; }
  html, body { width: 900px; height: 1200px; overflow: hidden; }
  body {
    position: relative;
    background: var(--page-bg);
    font-family: "Montserrat", sans-serif;
  }
  .card {
    position: absolute;
    left: 80px;
    width: 742px;
    height: 441px;
    border-radius: 24px;
    background: var(--card-navy);
    box-shadow: 0 6px 18px rgba(0,0,0,0.25);
    overflow: hidden;
  }
  .card--front { top: 131px; }
  .card--back { top: 638px; }

  .wordmark {
    position: absolute;
    font-family: "Cinzel", serif;
    font-weight: 500;
    white-space: nowrap;
    line-height: 1;
  }
  .card--front .wordmark {
    left: 36px;
    top: 70px;
    font-size: 37px;
    color: var(--ink-white);
  }
  .holder {
    position: absolute;
    right: 48px;
    top: 54px;
    text-align: right;
  }
  .holder__name {
    font-weight: 600;
    font-size: 26px;
    color: var(--ink-grey);
    line-height: 1.1;
  }
  .holder__role {
    font-weight: 400;
    font-size: 16px;
    color: var(--ink-soft);
    margin-top: 4px;
  }
  .address {
    position: absolute;
    left: 38px;
    top: 270px;
    font-size: 16px;
    font-weight: 400;
    line-height: 21px;
    color: var(--ink-soft);
  }
  .contacts {
    position: absolute;
    left: 37px;
    top: 330px;
    list-style: none;
  }
  .contacts li {
    display: flex;
    align-items: center;
    height: 28.5px;
    font-size: 16px;
    color: var(--ink-soft);
  }
  .contacts svg {
    width: 15px;
    height: 15px;
    margin-right: 10px;
    fill: none;
    stroke: var(--ink-soft);
    stroke-width: 1.6;
  }
  .brand-seal {
    position: absolute;
    left: 438px;
    top: 156px;
    width: 264px;
    height: 264px;
    display: flex;
    align-items: center;
    justify-content: center;
    font-family: "Cinzel", serif;
    font-weight: 500;
    font-size: 46px;
    color: var(--ink-white);
  }
  .card--back .wordmark {
    left: 0;
    right: 0;
    top: 206px;
    text-align: center;
    font-size: 56px;
    color: var(--back-mark);
  }
</style>
</head>
<body>
  <section class="card card--front">
    <div class="wordmark">Corvane Capital</div>
    <div class="holder">
      <p class="holder__name">Marcus Ellery</p>
      <p class="holder__role">Owner</p>
    </div>
    <p class="address">42 Meridian Court<br>Fairhaven, NJ 07704 USA</p>
    <ul class="contacts">
      <li>
        <svg viewBox="0 0 16 16"><path d="M3 2l3 0 1 3-2 1.5a9 9 0 0 0 4.5 4.5L11 9l3 1v3a1 1 0 0 1-1 1A12 12 0 0 1 2 3a1 1 0 0 1 1-1z"/></svg>
        (555)214-7830
      </li>
      <li>
        <svg viewBox="0 0 16 16"><rect x="1.5" y="3.5" width="13" height="9" rx="1"/><path d="M1.5 4l6.5 5 6.5-5"/></svg>
        info@yourwebsitename.com
      </li>
      <li>
        <svg viewBox="0 0 16 16"><circle cx="8" cy="8" r="6.5"/><path d="M1.5 8h13M8 1.5c-2.5 3-2.5 10 0 13M8 1.5c2.5 3 2.5 10 0 13"/></svg>
        www.yourwebsitename.com
      </li>
    </ul>
    <div class="brand-seal">Corvane</div>
  </section>

  <section class="card card--back">
    <div class="wordmark">Corvane Capital</div>
  </section>
</body>
</html>
```